Tradelume.ai

Australian based application building technology company. website (tradelume.ai) servicing the retail and shopping industries, IoT
Similar services to https://vextrio.com/.
Logo attached

Target Market(s)

Technology Retail

Industry/Entity Type

It Company

Number of Pages Required

2 page

Font styles to use
Other font styles liked:
• We will supply

Colors
ec1f27

Requirements
Must have
• responsive, extra small, small, medium, large, wide
Nice to have
• Modern, sophisticated, current and ON trende
Should not have
• Over saturation, keep it simple, smart and easy navigation

```html
<!DOCTYPE html>
<html lang="en">
<head>
<meta charset="utf-8">
<title>Tradelume</title>
<link rel="stylesheet" href="https://fonts.googleapis.com/css2?family=Open+Sans:wght@300;400;600&family=Lora:wght@400&display=swap">
<style>
  :root {
    --red: #ec1f27;
    --red-text: #d0202a;
    --hero-bg: #141414;
    --hero-text: #8a8a8a;
    --hero-title: #6e6e6e;
    --ink: #666666;
    --band-grey: #eaeaea;
    --footer-bg: #444444;
    --footer-bar: #363636;
    --footer-text: #dddddd;
    --footer-link: #bbbbbb;
    --white: #ffffff;
  }
  * { box-sizing: border-box; margin: 0; padding: 0; }
  html, body { width: 1200px; height: 2826px; overflow: hidden; }
  body { position: relative; font-family: "Open Sans", Arial, sans-serif; background: var(--white); color: var(--ink); }
  .abs { position: absolute; }

  .hero { position: absolute; left: 0; top: 0; width: 1200px; height: 614px; background: var(--hero-bg); overflow: hidden; }
  .brand-box { position: absolute; left: 132px; top: 15px; width: 305px; height: 85px; background: var(--white); display: flex; align-items: center; justify-content: center; gap: 14px; }
  .brand-box .mark { width: 34px; height: 34px; border-radius: 50%; background: var(--red); }
  .brand-box .name { font-size: 36px; font-weight: 400; color: var(--red); letter-spacing: 0.5px; }
  .btn { position: absolute; display: flex; align-items: center; justify-content: center; gap: 7px; background: var(--red); color: var(--white); font-size: 13px; font-weight: 600; text-transform: uppercase; }
  .btn svg { width: 11px; height: 11px; }
  .btn-header { left: 906px; top: 17px; width: 160px; height: 40px; }
  .nav { position: absolute; top: 84px; left: 0; width: 1200px; height: 20px; }
  .nav a { position: absolute; color: var(--white); font-size: 13px; text-decoration: none; }
  .nav a.current { text-decoration: underline; text-underline-offset: 4px; }
  .hero-title { position: absolute; left: 90px; top: 118px; font-family: "Lora", Georgia, serif; font-size: 104px; line-height: 1; color: var(--hero-title); }
  .hero-features { position: absolute; left: 0; top: 258px; width: 560px; text-align: center; list-style: none; }
  .hero-features li { font-size: 30px; font-weight: 300; line-height: 37px; color: var(--hero-text); }
  .hero-media { position: absolute; left: 604px; top: 150px; width: 596px; height: 464px; background: linear-gradient(160deg, #6a6a6a, #3c3c3c 60%, #2a2a2a); border-radius: 28px 0 0 0; }
  .play { position: absolute; left: 578px; top: 284px; width: 42px; height: 42px; }

  .intro-title { position: absolute; left: 0; top: 686px; width: 1200px; text-align: center; font-size: 28px; color: var(--red-text); }
  .feature { position: absolute; top: 750px; width: 300px; text-align: center; }
  .feature .icon { display: block; margin: 0 auto; width: 70px; height: 70px; }
  .feature h3 { margin-top: 22px; font-size: 15px; font-weight: 400; color: var(--red-text); }
  .feature p { margin-top: 6px; font-size: 10.5px; line-height: 17px; color: var(--ink); padding: 0 12px; }

  .band { position: absolute; left: 0; width: 1200px; }
  .band-grey { background: var(--band-grey); }
  .map-fill { position: absolute; left: 0; top: 995px; width: 600px; height: 320px; background: linear-gradient(135deg, #f0f2f4, #dfe6ec); }
  .bullet-head { position: absolute; left: 640px; font-size: 28px; line-height: 32px; color: var(--red-text); }
  .bullet-head svg { position: absolute; left: 0; top: 8px; width: 12px; height: 16px; }
  .bullet-head span { display: block; padding-left: 28px; }
  .body-copy { position: absolute; font-size: 10.5px; line-height: 18px; color: var(--ink); }
  .section-head { position: absolute; font-size: 27px; line-height: 35px; color: var(--red-text); font-weight: 400; }
  .device-fill { position: absolute; border-radius: 26px; }

  .closing-title { position: absolute; left: 0; top: 2310px; width: 1200px; text-align: center; font-size: 28px; color: var(--red-text); }
  .closing-copy { position: absolute; left: 132px; top: 2356px; width: 936px; text-align: center; font-size: 10.5px; line-height: 18px; color: var(--ink); }
  .btn-closing { left: 520px; top: 2425px; width: 160px; height: 40px; }

  .footer { position: absolute; left: 0; top: 2543px; width: 1200px; height: 217px; background: var(--footer-bg); }
  .footer-col { position: absolute; top: 44px; }
  .footer-col h4 { font-size: 14px; font-weight: 400; color: var(--footer-text); margin-bottom: 8px; }
  .footer-col ul { list-style: none; }
  .footer-col li { font-size: 10.5px; line-height: 23px; color: var(--footer-link); }
  .footer-col li::before { content: "•"; margin-right: 7px; }
  .social { position: absolute; left: 912px; top: 44px; }
  .social h4 { font-size: 14px; font-weight: 400; color: var(--footer-text); }
  .social .circles { display: flex; gap: 8px; margin-top: 14px; margin-left: 17px; }
  .social .circles span { width: 34px; height: 34px; border: 1px solid #9a9a9a; border-radius: 50%; }
  .footer-bar { position: absolute; left: 0; top: 2760px; width: 1200px; height: 66px; background: var(--footer-bar); color: var(--white); font-size: 12px; text-align: center; line-height: 66px; }
</style>
</head>
<body>

<header class="hero">
  <div class="brand-box"><span class="mark"></span><span class="name">TRADELUME</span></div>
  <a class="btn btn-header">Get started now
    <svg viewBox="0 0 12 12"><circle cx="6" cy="6" r="6" fill="#fff"/><path d="M5 3.5 7.5 6 5 8.5" stroke="#ec1f27" stroke-width="1.6" fill="none"/></svg>
  </a>
  <nav class="nav">
    <a class="current" style="left:625px">Home</a>
    <a style="left:690px">About Us</a>
    <a style="left:772px">Services</a>
    <a style="left:850px">Products</a>
    <a style="left:929px">Projects</a>
    <a style="left:1006px">Contact Us</a>
  </nav>
  <div class="hero-title">tradelume</div>
  <ul class="hero-features">
    <li>Live real-time engagement</li>
    <li>Navigate places, products &amp; people</li>
    <li>Exact location and dwell time analytics</li>
    <li>Time and space specific promotions</li>
    <li>Entry, exit and pass by notifications</li>
    <li>Product content information and links</li>
    <li>In-store amenities and staff locator</li>
    <li>Front and Back end applications</li>
  </ul>
  <div class="hero-media" role="img" aria-label="Two smartphones showing the app's store map and product screens"></div>
  <svg class="play" viewBox="0 0 42 42"><circle cx="21" cy="21" r="21" fill="#fff"/><path d="M16 12 30 21 16 30Z" fill="#111"/></svg>
</header>

<h2 class="intro-title">Bridging the online and real-time shopping experience</h2>

<div class="feature" style="left:123px">
  <svg class="icon" viewBox="0 0 70 70"><path d="M6 20 24 12 46 20 64 12 64 58 46 66 24 58 6 66Z" fill="#f1d9a6"/><path d="M45 10a11 11 0 0 1 11 11c0 9-11 21-11 21S34 30 34 21a11 11 0 0 1 11-11Z" fill="#e2453b"/><circle cx="45" cy="21" r="4" fill="#fff"/></svg>
  <h3>Map to an exact location</h3>
  <p>Pellentesque pulvinar, urna eu tempor egestas, erat orci commodo ante, quis eleifend tellus mauris ut nulla. Cras sed nisi id metus hendrerit blandit.</p>
</div>
<div class="feature" style="left:453px">
  <svg class="icon" viewBox="0 0 70 70"><path d="M12 28h10l26-14v42L22 42H12Z" fill="#f39a1e"/><rect x="48" y="12" width="8" height="46" rx="4" fill="#3d6fb5"/><rect x="18" y="42" width="8" height="14" fill="#555"/></svg>
  <h3>Promote specific to time and place</h3>
  <p>Pellentesque pulvinar, urna eu tempor egestas, erat orci commodo ante, quis eleifend tellus mauris ut nulla. Cras sed nisi id metus hendrerit blandit.</p>
</div>
<div class="feature" style="left:777px">
  <svg class="icon" viewBox="0 0 70 70"><rect x="8" y="38" width="7" height="26" fill="#e2453b"/><rect x="18" y="28" width="7" height="36" fill="#f39a1e"/><rect x="28" y="44" width="7" height="20" fill="#3d6fb5"/><rect x="38" y="18" width="7" height="46" fill="#7cc45a"/><rect x="48" y="10" width="7" height="54" fill="#47b3c9"/><rect x="4" y="64" width="58" height="2" fill="#777"/></svg>
  <h3>Interactive LIVE at product level</h3>
  <p>Pellentesque pulvinar, urna eu tempor egestas, erat orci commodo ante, quis eleifend tellus mauris ut nulla. Cras sed nisi id metus hendrerit blandit.</p>
</div>

<section class="band band-grey" style="top:995px;height:320px"></section>
<div class="map-fill" role="img" aria-label="Indoor floor plan with a blue navigation route and location marker"></div>
<div class="bullet-head" style="top:1043px">
  <svg viewBox="0 0 12 16"><path d="M2 1 9 8 2 15" stroke="#d0202a" stroke-width="2" fill="none"/></svg>
  <span>Indoor Navigation</span>
</div>
<div class="bullet-head" style="top:1107px">
  <svg viewBox="0 0 12 16"><path d="M2 1 9 8 2 15" stroke="#d0202a" stroke-width="2" fill="none"/></svg>
  <span>Product, Customer and<br>Staff Location</span>
</div>
<p class="body-copy" style="left:640px;top:1193px;width:430px">Mauris aliquam lectus ac sagittis sodales. Sed vitae leo ac orci viverra condimentum sed eu arcu. Mauris luctus ipsum quis faucibus elementum. Morbi sapien dolor, facilisis in venenatis scelerisque, pellentesque vel arcu. Ut mollis, ligula ac imperdiet ultrices, ex ipsum condimentum lectus, non maximus quam nulla quis enim.</p>

<h2 class="section-head" style="left:196px;top:1508px">A Personal Shopper in<br>every customers hand</h2>
<p class="body-copy" style="left:196px;top:1588px;width:352px">Mauris aliquam lectus ac sagittis sodales. Sed vitae leo ac orci viverra condimentum sed eu arcu. Mauris luctus ipsum quis faucibus elementum. Morbi sapien dolor, facilisis in venenatis scelerisque, pellentesque vel arcu. Ut mollis, ligula ac imperdiet ultrices, ex ipsum condimentum lectus, non maximus quam nulla quis enim.</p>
<div class="device-fill" style="left:738px;top:1394px;width:195px;height:383px;background:linear-gradient(180deg,#1e1e1e,#3a3a3a 20%,#c9d6e3 30%,#b8c9d8 80%,#1e1e1e 90%)" role="img" aria-label="Smartphone showing an indoor store map with a location pin"></div>

<section class="band band-grey" style="top:1842px;height:400px"></section>
<div class="device-fill" style="left:279px;top:1865px;width:177px;height:353px;background:linear-gradient(180deg,#f1ece2,#e6e6e6 15%,#d7d9dc 50%,#e6e6e6 85%,#f1ece2)" role="img" aria-label="Smartphone showing a street map with a route to a car park"></div>
<h2 class="section-head" style="left:673px;top:1957px">Car Space Navigation Engage<br>from entry</h2>
<p class="body-copy" style="left:673px;top:2036px;width:352px">Mauris aliquam lectus ac sagittis sodales. Sed vitae leo ac orci viverra condimentum sed eu arcu. Mauris luctus ipsum quis faucibus elementum. Morbi sapien dolor, facilisis in venenatis scelerisque, pellentesque vel arcu. Ut mollis, ligula ac imperdiet ultrices, ex ipsum condimentum lectus, non maximus quam nulla quis enim.</p>

<h2 class="closing-title">Donec nulla sem, interdum Tradelume?</h2>
<p class="closing-copy">Maecenas pulvinar nulla eget purus fermentum molestie. Praesent tellus augue, mollis eget interdum sed, tempor non diam. Mauris aliquam lectus ac sagittis sodales. Sed vitae leo ac orci viverra condimentum sed eu arcu. Mauris luctus ipsum quis faucibus elementum. Morbi sapien dolor, facilisis in venenatis scelerisque, pellentesque vel arcu. Ut mollis, ligula ac imperdiet ultrices, ex ipsum condimentum lectus, non maximus quam nulla quis enim. Vestibulum dapibus in leo eu hendrerit.</p>
<a class="btn btn-closing">Get started now
  <svg viewBox="0 0 12 12"><circle cx="6" cy="6" r="6" fill="#fff"/><path d="M5 3.5 7.5 6 5 8.5" stroke="#ec1f27" stroke-width="1.6" fill="none"/></svg>
</a>

<footer class="footer">
  <div class="footer-col" style="left:132px"><h4>Fusce cursus</h4><ul><li>Proin porttitor</li><li>Nulla luctus enim</li><li>Aliquam fermentum</li><li>Vivamus lacus</li><li>Pellentesque convallis</li></ul></div>
  <div class="footer-col" style="left:324px"><h4>Fusce cursus</h4><ul><li>Proin porttitor</li><li>Nulla luctus enim</li><li>Aliquam fermentum</li><li>Vivamus lacus</li><li>Pellentesque convallis</li></ul></div>
  <div class="footer-col" style="left:518px"><h4>Fusce cursus</h4><ul><li>Proin porttitor</li><li>Nulla luctus enim</li><li>Aliquam fermentum</li><li>Vivamus lacus</li><li>Pellentesque convallis</li></ul></div>
  <div class="footer-col" style="left:712px"><h4>Fusce cursus</h4><ul><li>Proin porttitor</li><li>Nulla luctus enim</li><li>Aliquam fermentum</li><li>Vivamus lacus</li><li>Pellentesque convallis</li></ul></div>
  <div class="social"><h4>Follow us on</h4><div class="circles"><span></span><span></span><span></span><span></span></div></div>
</footer>
<div class="footer-bar">Copyright © 2017 Tradelume. All rights reserved.</div>

</body>
</html>
```